Book for new dads needs a cover.

We need a cover for a book titled Roadmap to Early Parenthood: Practical Methods for Welcoming a Newborn, Juggling Career and Home Life, and Managing Mental Health on the Path to Becoming a Parent. We would like to see a design that emphasizes healthy babies and confident dads.

```html
<!DOCTYPE html>
<html lang="en">
<head>
<meta charset="utf-8">
<title>Roadmap to Early Parenthood – Book Cover</title>
<link rel="stylesheet" href="https://fonts.googleapis.com/css2?family=Bebas+Neue&display=swap">
<style>
  :root {
    --page-bg: #ffffff;
    --sky-top: #84e6fc;
    --sky-bottom: #2cb2dd;
    --accent-orange: #ff7f00;
    --ink-dark: #222222;
    --ink-light: #ffffff;
    --art-top: #bfefff;
    --art-bottom: #3c8fd6;
  }
  html, body {
    margin: 0;
    padding: 0;
    width: 1200px;
    height: 1200px;
    overflow: hidden;
    background: var(--page-bg);
  }
  .cover-canvas {
    display: block;
    width: 1200px;
    height: 1200px;
  }
  .title-type,
  .subtitle-type,
  .author-type {
    font-family: "Bebas Neue", "Oswald", sans-serif;
  }
  .title-main { fill: var(--accent-orange); }
  .title-connector { fill: var(--ink-dark); }
  .title-band-text { fill: var(--ink-light); }
  .title-band { fill: var(--accent-orange); }
  .title-final { fill: var(--ink-dark); }
  .subtitle-type { fill: var(--ink-dark); }
  .author-type { fill: var(--ink-dark); }
</style>
</head>
<body>
<svg class="cover-canvas" viewBox="0 0 1200 1200" xmlns="http://www.w3.org/2000/svg">
  <defs>
    <linearGradient id="cover-sky" x1="0" y1="0" x2="0" y2="1">
      <stop offset="0" stop-color="var(--sky-top)"/>
      <stop offset="0.55" stop-color="#6dd9f6"/>
      <stop offset="1" stop-color="var(--sky-bottom)"/>
    </linearGradient>
    <linearGradient id="dad-art" x1="0" y1="0" x2="0" y2="1">
      <stop offset="0" stop-color="var(--art-top)" stop-opacity="0.9"/>
      <stop offset="1" stop-color="var(--art-bottom)" stop-opacity="0.85"/>
    </linearGradient>
    <filter id="cover-shadow" x="-5%" y="-5%" width="110%" height="110%">
      <feDropShadow dx="4" dy="0" stdDeviation="5" flood-color="#000" flood-opacity="0.35"/>
    </filter>
  </defs>

  <!-- Cover board -->
  <rect class="cover-board" x="200" y="0" width="800" height="1200" fill="url(#cover-sky)" filter="url(#cover-shadow)"/>

  <!-- Title -->
  <text class="title-type title-main" x="270" y="300" font-size="290" textLength="660" lengthAdjust="spacingAndGlyphs">ROADMAP</text>
  <text class="title-type title-connector" x="490" y="370" font-size="66" text-anchor="middle">TO</text>

  <polygon class="title-band" points="285,395 938,383 928,572 290,572"/>
  <text class="title-type title-band-text" x="300" y="548" font-size="205" textLength="620" lengthAdjust="spacingAndGlyphs">EARLY</text>

  <!-- Illustration area: shirt collar, striped tie and glasses -->
  <rect class="dad-illustration" role="img" aria-label="Illustration of a shirt collar with a striped blue tie and dark-rimmed glasses" x="432" y="585" width="206" height="320" rx="10" fill="url(#dad-art)"/>

  <text class="title-type title-final" x="300" y="890" font-size="400" textLength="615" lengthAdjust="spacingAndGlyphs">PARENTHOOD</text>

  <!-- Subtitle -->
  <text class="subtitle-type" x="600" y="970" font-size="29" text-anchor="middle" textLength="567" lengthAdjust="spacingAndGlyphs">PRACTICAL METHODS FOR WELCOMING A NEWBORN, JUGGLING</text>
  <text class="subtitle-type" x="600" y="1003" font-size="29" text-anchor="middle" textLength="540" lengthAdjust="spacingAndGlyphs">CAREER AND HOME LIFE, AND MANAGING MENTAL HEALTH</text>
  <text class="subtitle-type" x="600" y="1036" font-size="29" text-anchor="middle" letter-spacing="1">ON THE PATH TO BECOMING A PARENT</text>

  <!-- Author -->
  <text class="author-type" x="303" y="1133" font-size="70" textLength="630" lengthAdjust="spacing">AUTHOR NAME</text>
</svg>
</body>
</html>
```